3 Page Design for Ninth Bay Capital

We want a Home Page, About Page, and Products & Services Page for Ninth Bay Capital. Please refer to the attached docs for more info.
If done in Figma, would like Figma files that can easily be ported to Wordpress.

```html
<!DOCTYPE html>
<html lang="en">
<head>
<meta charset="utf-8">
<title>Ninth Bay Capital — Home</title>
<link href="https://fonts.googleapis.com/css2?family=Archivo:wght@800;900&family=Outfit:wght@400;500;600&display=swap" rel="stylesheet">
<style>
:root{
  --sand:#e2d6bf;
  --brown:#7a6244;
  --brown-title:#7a603f;
  --ink:#1a1a1a;
  --crimson:#8b1b2c;
  --violet:#5a4a8b;
  --stone:#dcd6d0;
  --night:#262424;
  --muted:#8a7a66;
}
*{box-sizing:border-box;margin:0;padding:0}
html,body{width:1200px;height:4068px;overflow:hidden}
body{position:relative;background:var(--sand);font-family:'Outfit',sans-serif;color:var(--ink)}
.abs{position:absolute}
.heading{font-family:'Archivo',sans-serif;font-weight:900;text-transform:uppercase;letter-spacing:.5px}
.center{left:0;width:1200px;text-align:center}
.accent{color:var(--brown-title)}

/* nav */
.nav a{position:absolute;top:47px;font-size:16px;line-height:20px;text-transform:uppercase;color:var(--ink);text-decoration:none}
.nav a.active{color:var(--brown)}
.brand{left:450px;width:300px;top:45px;text-align:center;font-weight:600;font-size:22px;line-height:26px;color:var(--ink);text-transform:uppercase}
.brand-dot{left:587px;top:12px;width:26px;height:26px;border-radius:50%;background:var(--brown)}
.phone-bubble{width:54px;height:54px;border-radius:50%;background:#c6bcae;display:flex;align-items:center;justify-content:center}
.call-small{font-size:12px;line-height:16px}
.call-big{font-size:16px;font-weight:600;line-height:20px}

/* hero */
.hero{left:25px;top:133px;width:1151px;height:644px;border-radius:18px;background:linear-gradient(100deg,#dcd8d6,#cfcac7);overflow:hidden}
.hero-photo{position:absolute;right:0;top:0;width:530px;height:644px;background:radial-gradient(ellipse at 60% 55%,#a9303d 0%,#c9c2bd 45%,#d2cdca 75%)}
.hero-title{left:109px;top:268px;font-size:50px;line-height:60px}
.hero-sub{left:109px;top:414px;font-weight:600;font-size:20px;line-height:24px;text-transform:uppercase}
.hero-copy{left:109px;top:457px;width:540px;font-size:16.5px;line-height:26px}
.btn{display:flex;align-items:center;justify-content:center;border-radius:26px;color:#fff;font-weight:600;font-size:13px;text-transform:uppercase}
.btn-crimson{left:109px;top:568px;width:234px;height:48px;background:var(--crimson)}
.scroll-pill{left:581px;top:739px;width:38px;height:70px;border-radius:19px;background:#efebe8;border:2px solid #bdb7b2}
.scroll-pill::after{content:"";position:absolute;left:16px;top:22px;width:3px;height:20px;border-radius:2px;background:#9a948e}

/* intro */
.section-title{font-size:40px;line-height:48px}
.body-copy{font-size:16.5px;line-height:26px}
.btn-violet{left:526px;top:1216px;width:148px;height:47px;background:var(--violet)}

/* framework */
.framework{left:25px;top:1355px;width:1151px;height:677px;border-radius:14px;background:var(--brown);overflow:hidden;color:#fff}
.fw-item{position:absolute}
.fw-item h3{font-weight:600;font-size:21px;line-height:26px;text-transform:uppercase}
.fw-item p{font-size:16px;line-height:25px;margin-top:9px}
.fw-core{position:absolute;left:0;top:0}
.fw-brand{position:absolute;left:375px;width:400px;top:555px;text-align:center;color:var(--ink);font-weight:600;font-size:24px;line-height:30px;text-transform:uppercase}

/* offer cards */
.offer-card{top:2318px;width:443px;height:461px;border-radius:10px;overflow:hidden;color:#fff}
.offer-card .photo{position:absolute;inset:0}
.offer-card .shade{position:absolute;inset:0;background:linear-gradient(180deg,rgba(0,0,0,0) 45%,rgba(0,0,0,.55) 100%)}
.offer-card h3{position:absolute;left:41px;font-weight:600;font-size:21px;line-height:26px;text-transform:uppercase}
.offer-card p{position:absolute;left:41px;width:340px;font-size:16px;line-height:25px}

/* testimonial */
.avatar{left:553px;top:3011px;width:94px;height:94px;border-radius:50%;background:linear-gradient(180deg,#d6d9de,#4a7fa8)}
.dots{left:578px;top:3324px;display:flex;gap:6px}
.dots i{display:block;width:6px;height:6px;border-radius:50%;background:var(--brown)}
.dots i:first-child{background:var(--ink)}

/* footer */
.footer{left:0;top:3553px;width:1200px;height:515px;background:var(--night)}
.mission{left:65px;top:3427px;width:1070px;height:336px;border-radius:16px;background:var(--brown);color:#fff}
.footer-brand{left:156px;width:300px;top:3895px;text-align:center;color:#fff;font-weight:600;font-size:18px;line-height:24px;text-transform:uppercase}
.footer-dot{left:290px;top:3846px;width:32px;height:32px;border-radius:50%;background:#fff}
.social{top:3941px;width:38px;height:38px;border-radius:50%;background:var(--brown)}
.footer-nav a{position:absolute;top:3833px;color:#fff;font-size:16px;line-height:20px;text-transform:uppercase;text-decoration:none}
.contact-bubble{width:54px;height:54px;border-radius:50%;background:#c6bcae;display:flex;align-items:center;justify-content:center}
.contact-small{font-size:12px;line-height:16px;color:var(--brown)}
.contact-big{font-size:16px;font-weight:600;line-height:20px;color:#fff}
.rule{left:95px;top:3998px;width:1010px;height:1px;background:#4a4646}
.copyright{top:4031px;font-size:12px;line-height:16px;color:#fff}
</style>
</head>
<body>

<!-- header -->
<nav class="nav">
  <a class="active" href="#" style="left:92px">Home</a>
  <a href="#" style="left:183px">About</a>
  <a href="#" style="left:281px">Products &amp; Services</a>
  <a href="#" style="left:778px">Contact Us</a>
</nav>
<span class="abs brand-dot"></span>
<div class="abs brand">Ninth Bay Capital</div>
<div class="abs phone-bubble" style="left:911px;top:30px">
  <svg width="22" height="22" viewBox="0 0 24 24"><path fill="#2a2a2a" d="M6.6 10.8a15.1 15.1 0 0 0 6.6 6.6l2.2-2.2a1 1 0 0 1 1-.25 11.4 11.4 0 0 0 3.6.57 1 1 0 0 1 1 1V20a1 1 0 0 1-1 1A17 17 0 0 1 3 4a1 1 0 0 1 1-1h3.5a1 1 0 0 1 1 1c0 1.25.2 2.45.57 3.57a1 1 0 0 1-.25 1z"/></svg>
</div>
<div class="abs call-small" style="left:981px;top:35px">Call Us Today</div>
<div class="abs call-big" style="left:981px;top:56px">+1 (555) 014 2200</div>

<!-- hero -->
<section class="abs hero">
  <div class="hero-photo" role="img" aria-label="Athlete in white top and red leggings leaping against a light concrete wall"></div>
</section>
<h1 class="abs heading hero-title"><span class="accent">Where Discipline</span><br>Meets Wealth</h1>
<p class="abs hero-sub">Built for legacy. Designed for performance.</p>
<p class="abs hero-copy">Ninth Bay helps athletes and entrepreneurs turn discipline into long-term success through refined strategy, structured systems, and performance-driven coaching.</p>
<a class="abs btn btn-crimson">Start Your Transition</a>
<span class="abs scroll-pill"></span>

<!-- intro -->
<h2 class="abs heading section-title center" style="top:899px"><span class="accent">Built for the next</span><br>chapter of your life.</h2>
<p class="abs body-copy center" style="top:1021px">Athletes and high-performers don’t fail because they lack talent — they fail because they lack<br>structure, strategy, and support once the game changes.</p>
<p class="abs body-copy center" style="top:1098px">Ninth Bay exists to bridge the gap between performance and generational success.<br>We give you the systems, stability, and strategic clarity to build wealth, wellness, and identity<br>beyond the field.</p>
<a class="abs btn btn-violet">View More</a>

<!-- framework -->
<section class="abs framework">
  <svg class="fw-core" width="1151" height="677" viewBox="0 0 1151 677">
    <circle cx="575" cy="563" r="197" fill="#dcd6d0"/>
    <g fill="#fff">
      <circle cx="572" cy="353" r="16"/>
      <circle cx="430" cy="418" r="16"/>
      <circle cx="720" cy="418" r="16"/>
      <circle cx="378" cy="545" r="16"/>
      <circle cx="774" cy="545" r="16"/>
    </g>
    <circle cx="575" cy="520" r="18" fill="#7a6244"/>
  </svg>
  <div class="fw-brand" style="left:375px">Ninth Bay Capital</div>

  <h2 class="abs heading section-title" style="left:0;width:1151px;text-align:center;top:105px;color:#fff">Ninth Bay Framework</h2>
  <p class="abs" style="left:0;width:1151px;text-align:center;top:168px;font-size:16px;line-height:24px">We guide athletes and entrepreneurs through a refined, repeatable pathway:</p>

  <div class="fw-item" style="left:0;width:1151px;text-align:center;top:235px"><h3>Skill-to-Income Conversion</h3><p>Turn performance skills into business assets.</p></div>
  <div class="fw-item" style="left:68px;width:300px;text-align:right;top:328px"><h3>Wealth Architecture</h3><p>Create long-term sustainability and generational assets.</p></div>
  <div class="fw-item" style="left:775px;width:320px;top:328px"><h3>Strategic Mapping</h3><p>Build a plan that aligns your strengths with real-world opportunities.</p></div>
  <div class="fw-item" style="left:16px;width:300px;text-align:right;top:492px"><h3>Identity Reset</h3><p>Find clarity, purpose, and direction.</p></div>
  <div class="fw-item" style="left:831px;width:300px;top:492px"><h3>System Installation</h3><p>Automate your workflow and increase consistency.</p></div>
</section>

<!-- offer -->
<h2 class="abs heading section-title center" style="top:2147px"><span class="accent">What</span> We Offer</h2>
<p class="abs body-copy center" style="top:2217px">Whether you’re leaving the field, entering business, or leveling up your next chapter — Ninth Bay gives<br>you the structure and strategic clarity to thrive.</p>

<article class="abs offer-card" style="left:141px">
  <div class="photo" role="img" aria-label="Athlete resting against an exercise ball in a gym" style="background:linear-gradient(160deg,#8d8f95,#4a4b52 60%,#2d2d33)"></div>
  <div class="shade"></div>
  <h3 style="top:2325px;top:325px">Current &amp; Retired Athletes</h3>
  <p style="top:364px">Lorem ipsum dolor sit amet, consectetur adipiscing elit, sed do eiusm</p>
</article>
<article class="abs offer-card" style="left:616px">
  <div class="photo" role="img" aria-label="Smiling entrepreneur in an apron inside a café" style="background:linear-gradient(160deg,#9c8a72,#5a4a3a 55%,#2f2822)"></div>
  <div class="shade"></div>
  <h3 style="top:364px">Entrepreneurs in Transition</h3>
</article>

<!-- testimonials -->
<h2 class="abs heading section-title center" style="top:2921px"><span class="accent">Our</span> Testimonials</h2>
<div class="abs avatar" role="img" aria-label="Portrait of client Mara Ellison"></div>
<div class="abs center" style="top:3134px;font-weight:600;font-size:20px;line-height:26px">MARA ELLISON</div>
<div class="abs center" style="top:3170px;font-size:18px;line-height:24px;color:var(--muted)">Business Entrepreneur</div>
<p class="abs center" style="top:3213px;font-size:15px;line-height:26px">Lorem ipsum dolor sit amet, consectetur adipiscing elit, sed do eiusmod tempor incididunt ut<br>labore et dolore magna aliqua. Ut enim ad minim veniam, quis nostrud exercitation ullamco<br>laboris nisi ut aliquip ex ea commodo consequat.</p>
<div class="abs dots"><i></i><i></i><i></i><i></i></div>

<!-- footer -->
<footer class="abs footer"></footer>
<section class="abs mission">
  <h2 class="heading section-title" style="position:absolute;left:0;width:1070px;text-align:center;top:97px">Our Misson</h2>
  <p style="position:absolute;left:0;width:1070px;text-align:center;top:166px;font-size:15px;line-height:26px">Lorem ipsum dolor sit amet, consectetur adipiscing elit, sed do eiusmod tempor incididunt ut<br>labore et dolore magna aliqua. Ut enim ad minim veniam, quis nostrud exercitation ullamco<br>laboris nisi ut aliquip ex ea commodo consequat.</p>
</section>

<span class="abs footer-dot"></span>
<div class="abs footer-brand">Ninth Bay Capital</div>
<span class="abs social" style="left:242px"></span>
<span class="abs social" style="left:284px"></span>
<span class="abs social" style="left:327px"></span>

<nav class="footer-nav">
  <a href="#" style="left:490px">Home</a>
  <a href="#" style="left:581px">About</a>
  <a href="#" style="left:674px">Products &amp; Services</a>
  <a href="#" style="left:895px">Contact Us</a>
</nav>

<div class="abs contact-bubble" style="left:503px;top:3894px">
  <svg width="22" height="22" viewBox="0 0 24 24"><path fill="#2a2a2a" d="M6.6 10.8a15.1 15.1 0 0 0 6.6 6.6l2.2-2.2a1 1 0 0 1 1-.25 11.4 11.4 0 0 0 3.6.57 1 1 0 0 1 1 1V20a1 1 0 0 1-1 1A17 17 0 0 1 3 4a1 1 0 0 1 1-1h3.5a1 1 0 0 1 1 1c0 1.25.2 2.45.57 3.57a1 1 0 0 1-.25 1z"/></svg>
</div>
<div class="abs contact-small" style="left:572px;top:3900px">Call Us Today</div>
<div class="abs contact-big" style="left:572px;top:3922px">+1 (555) 014 2200</div>

<div class="abs contact-bubble" style="left:761px;top:3894px">
  <svg width="24" height="20" viewBox="0 0 24 20"><rect x="1" y="2" width="22" height="16" rx="2" fill="#2a2a2a"/><path d="M2 4l10 7 10-7" stroke="#c6bcae" stroke-width="2" fill="none"/></svg>
</div>
<div class="abs contact-small" style="left:830px;top:3900px">Email Us Today</div>
<div class="abs contact-big" style="left:830px;top:3922px">hello@ninthbaycapital.com</div>

<div class="abs rule"></div>
<div class="abs copyright center">Copyright@2025.All Rights Reserved</div>

</body>
</html>
```